Company Profile

Redesign of Business Profile for print in A4 format. The design pages should complete a booklet. Kindly use Pictures as well as projects from our website @zwilobeniproperties.co.za

Business, Construction

```html
<!DOCTYPE html>
<html lang="en">
<head>
<meta charset="utf-8">
<title>Zwilobeni Properties – Company Profile</title>
<link href="https://fonts.googleapis.com/css2?family=Roboto:wght@400;700&family=Allura&display=swap" rel="stylesheet">
<style>
  :root {
    --red: #b3242b;
    --charcoal: #3b3b3d;
    --charcoal-deep: #2a2a2c;
    --grey: #5a5a5c;
    --paper: #ffffff;
    --ink-soft: #d9d9d9;
  }
  * { box-sizing: border-box; margin: 0; padding: 0; }
  html, body { width: 849px; height: 1200px; overflow: hidden; }
  body { font-family: "Roboto", Arial, sans-serif; background: var(--charcoal); }
  .page { position: relative; width: 849px; height: 1200px; overflow: hidden; background: var(--charcoal); }
  .backdrop { position: absolute; inset: 0; }
  .tagline {
    position: absolute; left: 110px; top: 118px;
    font-family: "Allura", cursive; font-size: 52px; color: #c4c4c4;
    transform: rotate(-7deg); transform-origin: left center;
  }
  .website {
    position: absolute; right: 26px; top: 8px;
    font-size: 9px; color: #777; letter-spacing: .3px;
  }
  .project-photo {
    position: absolute; left: 500px; top: 40px; width: 420px; height: 420px;
    border-radius: 50%;
    background: radial-gradient(circle at 40% 35%, #e9edf0 0%, #b9c2c8 35%, #6d7276 70%, #3d3f42 100%);
  }
  .highlight {
    position: absolute; right: 0; top: 40px; width: 250px;
    background: var(--red); color: #fff;
    font-size: 7px; line-height: 1.35; padding: 5px 12px 6px 14px;
    text-transform: uppercase; letter-spacing: .2px;
  }
  .copy {
    position: absolute; left: 34px; top: 268px; width: 392px; color: #fff;
  }
  .copy h2 { font-size: 18px; font-weight: 700; letter-spacing: .5px; margin-bottom: 12px; }
  .copy p { font-size: 11px; line-height: 1.55; color: var(--ink-soft); margin-bottom: 13px; }
  .copy h2.message { margin-top: 14px; }
  .award { position: absolute; width: 70px; text-align: center; }
  .award .seal {
    width: 34px; height: 34px; margin: 0 auto 5px; border-radius: 50%;
    border: 2px solid #cfcfcf; background: rgba(255,255,255,.08);
  }
  .award span { display: block; font-size: 5.6px; line-height: 1.3; color: #e2e2e2; }
  .brand {
    position: absolute; right: 24px; bottom: 46px;
    display: flex; align-items: center; gap: 8px;
    font-size: 19px; font-weight: 400; color: var(--charcoal);
  }
  .brand .mark { width: 12px; height: 12px; background: var(--red); }
</style>
</head>
<body>
<div class="page">
  <svg class="backdrop" width="849" height="1200" viewBox="0 0 849 1200">
    <path d="M0 0 H849 V250 L480 250 C440 225 420 215 0 212 Z" fill="var(--paper)"/>
    <path d="M0 0 H520 C380 30 190 30 0 14 Z" fill="var(--red)"/>
    <path d="M0 14 C190 30 380 30 520 0 H560 C400 45 190 50 0 34 Z" fill="var(--charcoal-deep)" opacity=".85"/>
    <circle cx="710" cy="250" r="226" fill="none" stroke="var(--charcoal-deep)" stroke-width="14"/>
    <path d="M486 300 A226 226 0 0 0 640 34" fill="none" stroke="var(--red)" stroke-width="8"/>
    <path d="M0 1075 C260 1040 560 930 849 720 V1200 H0 Z" fill="var(--red)"/>
    <path d="M0 1095 C270 1060 570 950 849 745 V1200 H0 Z" fill="var(--grey)"/>
    <path d="M0 1120 C300 1090 560 1010 849 800 V1200 H0 Z" fill="var(--charcoal)"/>
    <path d="M560 1200 C600 1130 700 1060 849 1010 V1200 Z" fill="var(--paper)"/>
    <path d="M540 1200 C590 1120 700 1050 849 990 V1005 C710 1055 610 1125 570 1200 Z" fill="var(--red)"/>
  </svg>

  <div class="tagline">achieving distinction</div>
  <div class="website">www.zwilobeni.co.za</div>

  <div class="project-photo" role="img" aria-label="Photograph of a completed multi-storey building with steel stair towers"></div>
  <p class="highlight">We have successfully completed numerous high value construction projects in South Africa, valued at billions of rands</p>

  <section class="copy">
    <h2>INTRODUCTION</h2>
    <p>Established in March 2001, Zwilobeni Properties is a highly acclaimed 100% black-owned construction and infrastructure development company built on a foundation of entrepreneurial excellence.</p>
    <p>At Zwilobeni Properties, we believe that public, private and civil institutions must play their role in contributing to the socioeconomic development of our country. We continue to pursue opportunities to offer sustainable and cost-effective housing, commercial facilities and infrastructure solutions, with exceptional value to our clients and the communities in which we work.</p>
    <h2 class="message">THE MESSAGE</h2>
    <p>As a company, our portfolio of projects spans across the entire spectrum of infrastructure development; from the construction of roads and bridges, reservoirs, water purification plants, water treatment works and sewerage systems; to schools, hospitals and clinics, the community centres, and office buildings. We have also established townships, townhouse complexes and security villages.</p>
    <p>We employ experts and upskill staff across an extensive range of specialised areas. With a diverse team in terms of race, gender, skills and experience, we work closely with business partners in the construction and infrastructure development sectors. This network enables us to capacitate and achieve the level of management required to meet both our own standards of delivery, efficiency and budget management and that of our clients.</p>
  </section>

  <div class="award" style="left:38px;top:1010px"><div class="seal"></div><span>Top Black Owned Construction Company Award 2005</span></div>
  <div class="award" style="left:103px;top:980px"><div class="seal"></div><span>Excellence in Infrastructure Development Award</span></div>
  <div class="award" style="left:168px;top:986px"><div class="seal"></div><span>Leadership in Property Development Recognition</span></div>
  <div class="award" style="left:238px;top:975px"><div class="seal"></div><span>Quality Housing Delivery Provincial Award</span></div>
  <div class="award" style="left:306px;top:955px"><div class="seal"></div><span>Best Emerging Contractor National Awards</span></div>
  <div class="award" style="left:374px;top:920px"><div class="seal"></div><span>Sustainable Building Practice Award</span></div>
  <div class="award" style="left:440px;top:880px"><div class="seal"></div><span>Outstanding Contribution to Community Development Award</span></div>

  <div class="brand"><span class="mark"></span><span class="name">Zwilobeni Properties</span></div>
</div>
</body>
</html>
```